Advert for Services that we offer

Brimfold Haulage Ltd need an design to represent what we do in a modern way by showing an image with a brief description and the use of corporate logo the information we will proved vie a doc file and this is to be presented in a modern way. This design will be for print & web. we have done our own design and its not great i have put this in the file repository

Target Market(s)

Motor trade

Font styles to use
Sans Serif

Colors

Designer to choose colors to be used in the design.

Requirements
Must have
• Company colour scheme as per logo within the files uploaded.
• and a small boarder to isolate it from the rest of the articles.
Nice to have
• Modern font
Should not have
• Old style font

```html
<!DOCTYPE html>
<html lang="en">
<head>
<meta charset="utf-8">
<title>Brimfold Haulage Ltd – Product Testing &amp; Analysis</title>
<link rel="stylesheet" href="https://fonts.googleapis.com/css2?family=Jost:wght@300;400;500&family=Lato:wght@700&display=swap">
<style>
  :root {
    --page-bg: #ececec;
    --frame: #000000;
    --panel-dark: #0b0b0c;
    --panel-mid: #26272a;
    --brand-blue: #1a6fd0;
    --text-light: #ffffff;
    --text-soft: #e4e4e4;
    --photo-deep: #1b2230;
    --photo-mid: #5b6474;
    --photo-light: #b9bcc4;
    --photo-accent: #b4461c;
  }
  * { box-sizing: border-box; margin: 0; padding: 0; }
  html, body {
    width: 976px;
    height: 1200px;
    overflow: hidden;
    background: var(--page-bg);
  }
  .stage { position: relative; width: 976px; height: 1200px; }

  .advert {
    position: absolute;
    display: flex;
    background: var(--frame);
    border: solid var(--frame);
  }
  .advert--compact {
    left: 69px; top: 51px; width: 834px; height: 506px;
    border-width: 6px;
    box-shadow: 0 4px 8px rgba(0,0,0,0.35);
    --panel-w: 345px;
    --brand-top: 44px; --brand-size: 21px; --square: 15px;
    --head-top: 129px; --head-size: 43px; --head-lh: 41px;
    --list-top: 277px; --list-left: 10px; --list-size: 27px; --list-lh: 32px; --dot: 6px;
    --contact-bottom: 5px; --contact-size: 14.5px; --contact-left: 14px;
  }
  .advert--wide {
    left: 0; top: 609px; width: 976px; height: 592px;
    border-width: 7px 7px 0 7px;
    --panel-w: 403px;
    --brand-top: 54px; --brand-size: 25px; --square: 18px;
    --head-top: 145px; --head-size: 52px; --head-lh: 48px;
    --list-top: 319px; --list-left: 12px; --list-size: 32px; --list-lh: 37.3px; --dot: 7px;
    --contact-bottom: 8px; --contact-size: 17px; --contact-left: 15px;
  }

  .info-panel {
    position: relative;
    width: var(--panel-w);
    height: 100%;
    background: radial-gradient(ellipse at 30% 25%, var(--panel-mid) 0%, var(--panel-dark) 75%);
    color: var(--text-light);
  }
  .brand {
    position: absolute;
    top: var(--brand-top);
    left: 0; right: 0;
    display: flex;
    align-items: center;
    justify-content: center;
    gap: 9px;
    font-family: "Jost", sans-serif;
    font-weight: 500;
    font-size: var(--brand-size);
    letter-spacing: 0.5px;
    text-transform: uppercase;
    color: var(--brand-blue);
    white-space: nowrap;
  }
  .brand-square {
    width: var(--square);
    height: var(--square);
    background: var(--brand-blue);
  }
  .headline {
    position: absolute;
    top: var(--head-top);
    left: 0;
    width: 100%;
    text-align: center;
    font-family: "Lato", sans-serif;
    font-weight: 700;
    font-size: var(--head-size);
    line-height: var(--head-lh);
    white-space: nowrap;
  }
  .services {
    position: absolute;
    top: var(--list-top);
    left: var(--list-left);
    list-style: none;
    font-family: "Jost", sans-serif;
    font-weight: 400;
    font-size: var(--list-size);
    line-height: var(--list-lh);
    letter-spacing: 0.8px;
    white-space: nowrap;
  }
  .services li { display: flex; align-items: center; }
  .services li::before {
    content: "";
    width: var(--dot);
    height: var(--dot);
    border-radius: 50%;
    background: var(--text-light);
    margin-right: 5px;
    transform: translateY(-3px);
  }
  .contact {
    position: absolute;
    bottom: var(--contact-bottom);
    left: var(--contact-left);
    font-family: "Jost", sans-serif;
    font-weight: 300;
    font-size: var(--contact-size);
    color: var(--text-soft);
    white-space: nowrap;
  }
  .contact .divider { margin: 0 7px; }
  .photo {
    flex: 1;
    height: 100%;
    background:
      radial-gradient(ellipse at 40% 75%, var(--photo-accent) 0%, rgba(180,70,28,0) 28%),
      linear-gradient(100deg, var(--photo-light) 0%, var(--photo-mid) 35%, var(--photo-deep) 70%, #0f141d 100%);
  }
</style>
</head>
<body>
  <div class="stage">
    <section class="advert advert--compact">
      <div class="info-panel">
        <div class="brand"><span class="brand-square"></span>Brimfold Haulage Ltd</div>
        <h1 class="headline">Product Testing<br>&amp;<br>Analysis</h1>
        <ul class="services">
          <li>Metallurgical testing</li>
          <li>Bearing pre-load testing</li>
          <li>Bore measurement</li>
          <li>New product evaluation</li>
          <li>Product analysis &amp; report</li>
        </ul>
        <p class="contact">TEL: 0161 555 0192<span class="divider">|</span>www.brimfold-haulage.co.uk</p>
      </div>
      <div class="photo" role="img" aria-label="Photo of a technician in dark overalls and safety glasses measuring the bore of a flanged orange casting with a digital dial gauge in a workshop"></div>
    </section>

    <section class="advert advert--wide">
      <div class="info-panel">
        <div class="brand"><span class="brand-square"></span>Brimfold Haulage Ltd</div>
        <h2 class="headline">Product Testing<br>&amp;<br>Analysis</h2>
        <ul class="services">
          <li>Metallurgical testing</li>
          <li>Bearing pre-load testing</li>
          <li>Bore measurement</li>
          <li>New product evaluation</li>
          <li>Product analysis &amp; report</li>
        </ul>
        <p class="contact">TEL: 0161 555 0192<span class="divider">|</span>www.brimfold-haulage.co.uk</p>
      </div>
      <div class="photo" role="img" aria-label="Photo of a technician in dark overalls and safety glasses measuring the bore of a flanged orange casting with a digital dial gauge in a workshop"></div>
    </section>
  </div>
</body>
</html>
```